indépendant en tant que Massothérapeute et Préparateur Mental, j'ai besoin de ...

Massothérapeute et préparateur mental indépendant, je recherche une carte de visite sobre et dynamique, sans images liées au massage ou à la préparation mentale mais intégrant mon logo. Les couleurs que j'aime bien sont : Blanc, gris, anthracite, noir et jaune

Contact Information for Business Card

carte de préférence Horizontale
neutre qui puisse toucher le deux domaines Massothérapie et préparation mentale

Requirements
Must have
• mon projet doit intégrer au recto:
LOGO
Loïc Bardèze
078 513 26 48
info@loicbardeze.ch
et éventuellement www.loicbardeze.ch

et au verso les deux adresses:

Chemin des Ormilles 7B
1400 Yverdon-les-Bains

Route de la Gravière 9
1700 Fribourg

Should not have
• mon projet ne doit pas contenir d'image en liens avec le massage ni la préparation mentale.

```html
<!DOCTYPE html>
<html lang="fr">
<head>
<meta charset="utf-8">
<title>Loïc Bardèze – Cartes de visite</title>
<link href="https://fonts.googleapis.com/css2?family=Arimo:wght@400&family=Montserrat:wght@600&display=swap" rel="stylesheet">
<style>
  :root {
    --backdrop: #5b5b5b;
    --card: #1e1d1b;
    --brand-grey: #d9dddc;
    --accent: #e9c900;
    --text: #ececec;
    --rule: #6a6a66;
  }
  html, body {
    margin: 0;
    padding: 0;
    width: 1093px;
    height: 1200px;
    overflow: hidden;
    background: var(--backdrop);
  }
  .card {
    position: absolute;
    left: 265px;
    width: 578px;
    height: 357px;
    background: var(--card);
    box-shadow: 3px 3px 4px rgba(0,0,0,0.55);
  }
  .card--front { top: 226px; }
  .card--back { top: 620px; }

  .brand {
    position: absolute;
    left: 0;
    right: 0;
    display: flex;
    justify-content: center;
    align-items: center;
    gap: 14px;
    color: var(--brand-grey);
    font-family: "Arimo", Arial, sans-serif;
  }
  .card--front .brand { top: 74px; }
  .card--back .brand { top: 136px; }
  .brand__square {
    width: 38px;
    height: 38px;
    background: var(--brand-grey);
    border-radius: 4px;
  }
  .brand__text { display: flex; flex-direction: column; }
  .brand__name { font-size: 29px; line-height: 32px; font-weight: 400; }
  .brand__role {
    font-size: 8.5px;
    letter-spacing: 1px;
    text-transform: uppercase;
    margin-top: 2px;
  }

  .holder {
    position: absolute;
    top: 177px;
    left: 0; right: 0;
    text-align: center;
    font-family: "Montserrat", sans-serif;
    font-weight: 600;
    font-size: 22px;
    color: var(--accent);
    letter-spacing: -0.3px;
  }
  .icon-row {
    position: absolute;
    top: 219px;
    left: 0; right: 0;
    display: flex;
    justify-content: center;
    align-items: center;
    gap: 4px;
  }
  .icon-row__rule { width: 50px; height: 1px; background: var(--rule); margin: 0 4px; }
  .icon {
    width: 24px;
    height: 24px;
    border-radius: 3px;
    background: var(--accent);
    display: flex;
    align-items: center;
    justify-content: center;
  }
  .icon svg { width: 16px; height: 16px; }
  .contacts {
    position: absolute;
    top: 253px;
    left: 0; right: 0;
    text-align: center;
    font-family: "Arimo", Arial, sans-serif;
    font-size: 17px;
    line-height: 21px;
    color: var(--text);
  }
  .addresses {
    position: absolute;
    top: 259px;
    left: 0; right: 0;
    text-align: center;
    font-family: "Arimo", Arial, sans-serif;
    font-size: 17.5px;
    line-height: 32px;
    color: var(--text);
  }
  .addresses p { margin: 0; }
</style>
</head>
<body>
  <section class="card card--front">
    <div class="brand">
      <div class="brand__square"></div>
      <div class="brand__text">
        <span class="brand__name">Loïc Bardèze</span>
        <span class="brand__role">Massothérapeute / Préparateur Mental</span>
      </div>
    </div>
    <div class="holder">LOÏC BARDÈZE</div>
    <div class="icon-row">
      <span class="icon-row__rule"></span>
      <span class="icon" aria-label="Téléphone">
        <svg viewBox="0 0 16 16"><path d="M2 6c0-2 2-3 6-3s6 1 6 3l-3 1-1-2H6L5 7zM4 8h8l1 5H3z" fill="#1e1d1b"/></svg>
      </span>
      <span class="icon" aria-label="E-mail">
        <svg viewBox="0 0 16 16"><rect x="2" y="4" width="12" height="8" fill="none" stroke="#1e1d1b" stroke-width="1.2"/><path d="M2 4l6 5 6-5M2 12l4.5-4M14 12l-4.5-4" fill="none" stroke="#1e1d1b" stroke-width="1.1"/></svg>
      </span>
      <span class="icon" aria-label="Site web">
        <svg viewBox="0 0 16 16"><circle cx="8" cy="8" r="6.2" fill="#1e1d1b"/><path d="M6 4c1 1 2 1 2 3s-2 1-2 3M10 9c1 0 2 1 1 3" fill="none" stroke="#e9c900" stroke-width="1.3"/></svg>
      </span>
      <span class="icon-row__rule"></span>
    </div>
    <div class="contacts">
      <div>078 513 26 48</div>
      <div>info@loicbardeze.ch</div>
      <div>www.loicbardeze.ch</div>
    </div>
  </section>

  <section class="card card--back">
    <div class="brand">
      <div class="brand__square"></div>
      <div class="brand__text">
        <span class="brand__name">Loïc Bardèze</span>
        <span class="brand__role">Massothérapeute / Préparateur Mental</span>
      </div>
    </div>
    <div class="addresses">
      <p>Chemin des Ormilles 7B, 1400 Yverdon-les-Bains</p>
      <p>Route de la Gravière 9, 1700 Freiburg</p>
    </div>
  </section>
</body>
</html>
```